Home Remodeling company needs a business card design

we need a business card design for home remodeling company in hamilton county, indiana USA. we offers a wide range of construction services including whole house renovations, Design and Build Basements and Kitchen and Bathroom Remodeling . we would like to see designs for both site of business card that use the same color of the company logo and also including all information below :
1- Karim Feltous CEO / General Contractor
2- all company contacts Telephone numbers ( 1-888-DULOM-47 ) ( 317-555-0193) email address ( info@dulomhome.com) website ( www.dulomhome.com ) and social media logos (Facebook- twitter- google plus )
3- company logo
4- licensed . insured . bonded

```html
<!DOCTYPE html>
<html lang="en">
<head>
<meta charset="utf-8">
<title>Dulom Home Remodeling – Business Cards</title>
<link rel="stylesheet" href="https://fonts.googleapis.com/css2?family=Arimo:wght@400;700&family=Playfair+Display:wght@400&display=swap">
<style>
  :root {
    --backdrop: #d6cbbf;
    --paper: #f3f0e8;
    --ink: #2f2f2f;
    --brand-red: #c7262e;
    --night: #050505;
    --white: #ffffff;
    --divider: #e8e4dc;
    --social-navy: #1f2a6e;
    --social-sky: #2a9fd6;
  }
  * { box-sizing: border-box; margin: 0; padding: 0; }
  html, body { width: 1200px; height: 823px; overflow: hidden; }
  body {
    background: var(--backdrop);
    display: flex; flex-direction: column; align-items: center; justify-content: center;
    gap: 36px;
    font-family: "Arimo", Arial, sans-serif;
  }
  .business-card {
    width: 620px; height: 354px;
    background: var(--paper);
    position: relative;
    overflow: hidden;
    box-shadow: 0 8px 22px rgba(0,0,0,.16);
  }

  /* Back side */
  .card-back {
    display: flex; align-items: center; justify-content: center;
  }
  .card-back .brand-name { font-size: 72px; }

  /* Front side */
  .brand-area {
    position: absolute; left: 0; top: 0; right: 0; height: 186px;
    display: flex; flex-direction: column; justify-content: center; align-items: center;
  }
  .brand-name {
    font-weight: 700; font-size: 64px; line-height: 1;
    color: var(--ink); letter-spacing: 3px;
  }
  .brand-credentials {
    font-size: 16px; color: var(--night); margin-top: 14px;
  }
  .accent-band {
    position: absolute; left: 0; right: 0; top: 186px; height: 9px;
    background: var(--brand-red);
  }
  .contact-panel {
    position: absolute; left: 0; right: 0; top: 195px; bottom: 0;
    background: var(--night);
    display: flex; align-items: center;
    padding: 0 36px 0 40px;
  }
  .person { flex: 1; }
  .person-name {
    font-family: "Playfair Display", Georgia, serif;
    font-weight: 400;
    font-size: 31px; color: var(--brand-red); line-height: 1.05;
  }
  .person-title { font-size: 17px; color: var(--white); margin-top: 4px; }
  .social-list { display: flex; gap: 10px; margin-top: 16px; list-style: none; }
  .social-list li {
    width: 34px; height: 34px; border-radius: 5px;
  }
  .social-list li:nth-child(1) { background: var(--social-navy); }
  .social-list li:nth-child(2) { background: var(--social-sky); }
  .social-list li:nth-child(3) { background: var(--brand-red); }
  .panel-divider {
    width: 2px; height: 100px; background: var(--divider); margin: 0 30px 0 10px;
  }
  .contact-list { list-style: none; }
  .contact-list li {
    display: flex; align-items: center; gap: 9px;
    font-size: 16px; color: var(--white); line-height: 1.45;
  }
  .contact-icon {
    width: 13px; height: 13px; background: var(--brand-red); border-radius: 2px;
    display: flex; align-items: center; justify-content: center; flex: none;
  }
  .contact-icon svg { width: 9px; height: 9px; }
</style>
</head>
<body>
  <article class="business-card card-back" aria-label="Card back">
    <div class="brand-name">DULOM</div>
  </article>

  <article class="business-card card-front" aria-label="Card front">
    <header class="brand-area">
      <div class="brand-name">DULOM</div>
      <div class="brand-credentials">licensed .insured . bonded</div>
    </header>
    <div class="accent-band"></div>
    <section class="contact-panel">
      <div class="person">
        <h1 class="person-name">Karim Feltous</h1>
        <p class="person-title">CEO / General Contractor</p>
        <ul class="social-list" aria-label="Social media">
          <li aria-label="Social profile"></li>
          <li aria-label="Social profile"></li>
          <li aria-label="Social profile"></li>
        </ul>
      </div>
      <div class="panel-divider"></div>
      <ul class="contact-list">
        <li><span class="contact-icon"><svg viewBox="0 0 16 16"><path d="M4 1h3l1 4-2 1a8 8 0 0 0 4 4l1-2 4 1v3c0 1-1 2-2 2A13 13 0 0 1 1 3c0-1 1-2 3-2z" fill="#fff"/></svg></span>317-555-0193</li>
        <li><span class="contact-icon"><svg viewBox="0 0 16 16"><path d="M4 1h3l1 4-2 1a8 8 0 0 0 4 4l1-2 4 1v3c0 1-1 2-2 2A13 13 0 0 1 1 3c0-1 1-2 3-2z" fill="#fff"/></svg></span>1-888-DULOM-47</li>
        <li><span class="contact-icon"><svg viewBox="0 0 16 16"><circle cx="8" cy="8" r="6" fill="none" stroke="#fff" stroke-width="1.6"/><path d="M2 8h12M8 2c-3 3-3 9 0 12M8 2c3 3 3 9 0 12" fill="none" stroke="#fff" stroke-width="1.2"/></svg></span>www.dulomhome.com</li>
        <li><span class="contact-icon"><svg viewBox="0 0 16 16"><rect x="2" y="4" width="12" height="8" fill="none" stroke="#fff" stroke-width="1.5"/><path d="M2 4l6 5 6-5" fill="none" stroke="#fff" stroke-width="1.5"/></svg></span>info@dulomhome.com</li>
      </ul>
    </section>
  </article>
</body>
</html>
```